Corwin Beacon Lighting - Commercial & Residential Landscape Lighting

Landscape Lighting Services & Design: Create a website for our landscape lighting company. We would like the design to be tailored around this description:
Illuminate with Confidence. Designed with Precision. Installed with Care.
Locally and veteran-owned, we take pride in transforming outdoor spaces through innovative lighting solutions tailored to your vision. From landscape and holiday lighting to permanent installations, our effortless process and expert design deliver breathtaking results and lasting curb appeal. Backed by a lifetime warranty and quarterly service options, our commitment to quality and customer satisfaction is unwavering. Try before you buy and experience your home in a whole new light with our complimentary demo kit — see the stunning effects before you decide.
- Also, add in this information as well; Outdoor Lighting not only beautifies spaces but also significantly enhances safety by illuminating your home or business. Beautifully lit entrances deter potential intruders, making your home a safer place for your loved ones. we also offer quarterly service plans to ensure lighting equipment continues to operate & illuminate effectively throughout the year. Also mention we provide free estimates and we are offering a 10% discount to military, veterans, and first responders.

Target Market(s)

Luxury market

Industry/Entity Type

Landscape Lighting - Residential & Commercial Lighting Services

Coding

Coded - Design and coding required

Number of Pages Required

2 page

Colors
00AB8E
00BBA5
67D7C9
C6EFE9
E9F9F6
59FF00
82FF00
B8FF75
E3FFCB
F4FFEA
FFC000
F8CF3A
FAE287
FDF2CF
FEFAEE

Requirements
Must have
• a lead generation button where people can submit their information for us to reach out to them and schedule their free estimate, homepage, about page, contact page, products and services page, user friendly, easy to navigate, and it also must be engaging and eye popping, as well as appealing to the luxury market. Please use colors; verdent green, dark green, ivory, and sunny yellow. Also, include an about page that references our story; Derek is retired Army and he opened a fitness studio in 2017 with his wife Jolene. He has installed low voltage lighting in every home he lived in and for his friends and family over the years and decided to open his own business because he is passionate about beautifying outdoor landscapes and highlighting a properties full potential, not only in the day but at night as well all while providing safety and security for his clients. Having a deep respect for nature and landscaping, he wants to provide the same care and quality to each of his clients as he has in the fitness industry for decades. He believes small businesses are the back bone of America and he's excited to provide a service that is all to often neglected in the design of a home.
Nice to have
• I would like to have a clear intent and purpose, engaging web design, clear call to action, optimized for search engines, mobile friendy design, security measures, credibility indicators

```html
<!DOCTYPE html>
<html lang="en">
<head>
<meta charset="utf-8">
<title>Corwin Beacon Lighting – Residential &amp; Commercial Landscape Lighting</title>
<link rel="stylesheet" href="https://fonts.googleapis.com/css2?family=Questrial&family=Montserrat:wght@500;600;700&display=swap">
<style>
:root{
  --forest:#0e3427;
  --forest-mid:#134436;
  --footer:#113528;
  --teal:#00AB8E;
  --teal-soft:#67D7C9;
  --teal-pale:#C6EFE9;
  --gold:#F8CF3A;
  --sun:#FFC000;
  --amber:#E5A928;
  --ivory:#FEFAEE;
  --ink:#1b1b1b;
  --body:#2b2b2b;
  --white:#ffffff;
}
*{box-sizing:border-box;margin:0;padding:0}
html,body{width:1200px;height:4264px;overflow:hidden}
body{position:relative;background:var(--white);font-family:"Questrial",sans-serif;color:var(--body)}
.abs{position:absolute}
.btn{position:absolute;display:flex;align-items:center;justify-content:center;font-family:"Montserrat",sans-serif;font-weight:700;font-size:13px;letter-spacing:.3px;text-transform:uppercase;text-decoration:none}
.btn-amber{background:var(--amber);color:#1e2b22}
.btn-outline{border:2px solid var(--white);color:var(--white)}
.btn-outline-dark{border:2px solid #2a2410;color:#2a2410}
.eyebrow{position:absolute;left:0;width:1200px;text-align:center;font-size:14px;letter-spacing:4px;text-transform:uppercase}
.section-title{position:absolute;left:0;width:1200px;text-align:center;font-size:37px;color:var(--ink);letter-spacing:.5px;text-transform:uppercase}
.title-rule{position:absolute;height:3px;background:linear-gradient(90deg,rgba(248,207,58,0),var(--gold) 25%,var(--gold) 75%,rgba(248,207,58,0))}
.brand{font-family:"Questrial",sans-serif;color:var(--gold);text-transform:uppercase;letter-spacing:3px;white-space:nowrap}

/* hero */
.hero-photo{left:0;top:0;width:1200px;height:740px;background:
  radial-gradient(ellipse 360px 260px at 790px 430px,rgba(214,124,52,.85),rgba(120,70,30,.4) 55%,rgba(0,0,0,0) 80%),
  radial-gradient(ellipse 420px 300px at 1040px 300px,rgba(160,170,170,.5),rgba(0,0,0,0) 75%),
  linear-gradient(90deg,#0b2a1f 0%,#0f3326 40%,#243b2e 65%,#3b4a3a 100%)}
.main-nav{left:0;top:0;width:1200px;height:100px}
.main-nav .brand{position:absolute;left:112px;top:45px;font-size:14px;letter-spacing:1px;width:240px}
.nav-links{position:absolute;left:378px;top:46px;display:flex;gap:0}
.nav-links a{position:absolute;white-space:nowrap;color:var(--gold);font-size:14px;text-decoration:none;text-transform:uppercase;letter-spacing:.5px}
.nav-links a.active{color:var(--white);border-bottom:2px solid var(--white);padding-bottom:4px}
.hero-title{left:109px;top:250px;font-size:36px;line-height:50px;color:var(--gold);text-transform:uppercase;letter-spacing:.5px}
.hero-title span{display:block;border-bottom:2px solid rgba(248,207,58,.55);width:max-content;padding-right:10px}
.btn-teal{background:linear-gradient(90deg,#00AB8E,#67D7C9);color:#0b2a1f}

/* about */
.about-photo{left:204px;top:940px;width:354px;height:354px;border-radius:50%;border:14px solid var(--gold);
  background:radial-gradient(circle at 50% 78%,#5f8a32 0%,#3c6325 30%,rgba(0,0,0,0) 55%),radial-gradient(circle at 55% 55%,#c78a4d,#6f5338 35%,#2e3f2a 70%)}
.about-glow{left:60px;top:800px;width:640px;height:560px;background:radial-gradient(ellipse at 50% 50%,rgba(253,242,207,.9),rgba(254,250,238,0) 65%)}
.about-copy{left:593px;top:908px;width:536px;font-size:16.5px;line-height:27px;color:#333}
.about-quote{left:599px;top:1120px;width:510px;border-left:3px solid var(--teal);padding-left:16px;font-family:"Montserrat",sans-serif;font-weight:600;font-size:15.5px;line-height:27px;color:#222}
.perk{position:absolute;top:1345px;width:466px;height:139px;display:flex;align-items:center;padding-left:36px;gap:22px}
.perk-teal{left:119px;border:2px solid var(--teal-soft)}
.perk-gold{left:611px;border:2px solid var(--gold)}
.perk-icon{width:78px;height:78px;border-radius:50%;flex:none;display:flex;align-items:center;justify-content:center}
.perk h3{font-weight:400;font-size:20px;color:var(--ink);text-transform:uppercase;letter-spacing:.3px}
.perk p{font-size:16px;text-transform:uppercase;color:#444;line-height:20px;margin-top:4px}

/* sectors */
.sectors{left:0;top:1528px;width:1200px;height:549px;clip-path:polygon(0 0,100% 0,100% 96%,50% 90%,0 100%)}
.sector{position:absolute;top:0;height:549px;width:600px;text-align:center;color:var(--white)}
.sector-res{left:0;background:linear-gradient(160deg,#1f7a5c 0%,#0f9a7c 45%,#15805f 100%)}
.sector-com{left:600px;background:linear-gradient(200deg,#f5b82c 0%,#f7c23a 40%,#f1a933 100%);color:#1a1a1a}
.sector h2{position:absolute;left:0;width:600px;top:150px;font-weight:400;font-size:33px;line-height:39px;text-transform:uppercase;letter-spacing:.5px}
.sector p{position:absolute;left:90px;width:420px;top:268px;font-size:16.5px;line-height:27px}

/* products */
.card-photo{position:absolute;top:2214px;width:304px;height:321px;border:2px solid rgba(255,255,255,.6);outline:1px solid #999}
.card-landscape{left:111px;background:radial-gradient(ellipse at 30% 40%,#c9a24a,rgba(0,0,0,0) 40%),linear-gradient(180deg,#23331c 0%,#3f6a2c 45%,#6b8a3a 70%,#2c3a1f 100%)}
.card-permanent{left:784px;background:radial-gradient(ellipse at 45% 45%,#d9a866,#7b6140 40%,rgba(0,0,0,0) 70%),linear-gradient(180deg,#2a3550 0%,#3a3f4a 50%,#1e2220 100%)}
.card-caption{position:absolute;left:0;width:100%;bottom:30px;text-align:center;font-family:"Montserrat",sans-serif;font-weight:600;font-size:21px;line-height:28px;text-transform:uppercase}
.card-caption .accent{color:var(--gold)}
.card-caption .plain{color:var(--white)}
.card-feature{position:absolute;left:427px;top:2195px;width:349px;height:369px;background:#0d3a22;padding:10px}
.card-feature .frame{position:relative;width:100%;height:100%;border:1px solid rgba(255,255,255,.35);text-align:center;color:var(--white)}
.card-feature h3{padding-top:38px;font-family:"Montserrat",sans-serif;font-weight:600;font-size:25px;line-height:33px;text-transform:uppercase}
.card-feature p{margin:14px auto 0;width:280px;font-size:14.5px;line-height:22px}

/* why */
.why{left:0;top:2628px;width:1200px;height:637px;background:var(--forest-mid)}
.why-photo{left:0;top:2628px;width:1200px;height:637px;clip-path:polygon(770px 0,1200px 0,1200px 637px,579px 637px);
  background:radial-gradient(ellipse 300px 200px at 900px 360px,rgba(214,150,80,.8),rgba(0,0,0,0) 75%),linear-gradient(180deg,#5c77a8 0%,#4a5d80 40%,#3e4a3d 70%,#222a22 100%)}
.why .eyebrow-left{position:absolute;left:113px;top:93px;font-size:15px;letter-spacing:4px;color:var(--white);text-transform:uppercase}
.why h2{position:absolute;left:110px;top:117px;font-weight:400;font-size:41px;line-height:46px;color:var(--white);text-transform:uppercase}
.why .copy{position:absolute;left:109px;width:500px;font-size:19px;line-height:27px;color:var(--white)}

/* estimate */
.site-footer{left:0;top:3836px;width:1200px;height:428px;background:var(--footer)}
.estimate{left:136px;top:3330px;width:945px;height:559px;border-radius:16px;background:
  radial-gradient(ellipse 300px 200px at 250px 120px,rgba(255,225,140,.45),rgba(0,0,0,0) 75%),linear-gradient(180deg,#f3b62a 0%,#f8c233 50%,#f2b12b 100%)}
.estimate .eyebrow{left:0;width:945px;top:82px;color:#3a3010}
.estimate .section-title{left:0;width:945px;top:103px;font-size:33px}
.field{position:absolute;height:48px;background:var(--white);display:flex;align-items:center;gap:12px;padding-left:20px;font-size:14px;color:#444}
.field svg{flex:none}
.btn-forest{background:var(--forest);color:var(--white)}

.footer-brand{left:0;width:1200px;top:3955px;text-align:center;font-size:34px}
.footer-rule{left:113px;width:996px;height:1px;background:rgba(255,255,255,.25)}
.footer-nav{left:0;width:1200px;top:4068px;display:flex;justify-content:center;align-items:center;gap:34px}
.footer-nav a{color:var(--white);font-family:"Montserrat",sans-serif;font-weight:600;font-size:14px;text-decoration:none}
.footer-nav .dot{width:5px;height:5px;border-radius:50%;background:var(--gold)}
.contact-item{position:absolute;top:4137px;display:flex;align-items:center;gap:14px;color:var(--white);font-size:14px;white-space:nowrap}
.contact-item .badge{width:36px;height:36px;border-radius:50%;background:var(--sun);display:flex;align-items:center;justify-content:center}
.social{position:absolute;top:4143px;width:24px;height:24px;border-radius:50%;background:var(--sun)}
.copyright{left:0;width:1200px;top:4224px;text-align:center;font-size:13px;color:rgba(255,255,255,.8)}
</style>
</head>
<body>

<!-- HERO -->
<div class="abs hero-photo" role="img" aria-label="Brick house at dusk with warm landscape uplighting on facade and garden beds"></div>
<svg class="abs" style="left:0;top:630px" width="1200" height="112" viewBox="0 0 1200 112" aria-hidden="true">
  <polygon points="0,103 600,10 1200,103 1200,112 0,112" fill="#F8CF3A"/>
  <polygon points="0,106 600,22 1200,106 1200,112 0,112" fill="#ffffff"/>
</svg>

<header class="abs main-nav">
  <div class="brand">Corwin Beacon Lighting</div>
  <nav class="nav-links">
    <a class="active" href="#" style="left:0">Home</a>
    <a href="#" style="left:94px">About</a>
    <a href="#" style="left:195px">Services</a>
    <a href="#" style="left:317px">Products</a>
    <a href="#" style="left:449px">Contact Us</a>
  </nav>
  <a class="btn btn-amber" href="#estimate" style="left:963px;top:36px;width:152px;height:40px;font-size:12px">Free Estimate &rsaquo;</a>
</header>

<h1 class="abs hero-title" style="font-weight:400">
  <span>Illuminate with Confidence.</span>
  <span>Designed with Precision.</span>
  <span>Installed with Care.</span>
</h1>
<a class="btn btn-teal" href="#estimate" style="left:113px;top:435px;width:180px;height:45px">Free Estimate &rsaquo;</a>

<!-- WHO WE ARE -->
<div class="eyebrow" style="top:737px;color:var(--teal)">Who We Are</div>
<h2 class="section-title" style="top:757px;font-weight:400">Corwin Beacon Lighting</h2>
<div class="title-rule" style="left:470px;width:270px;top:812px"></div>

<div class="abs about-glow" aria-hidden="true"></div>
<div class="abs about-photo" role="img" aria-label="Lit home and lawn framed by tall pines at sunset"></div>

<p class="abs about-copy">Locally and veteran-owned, we take pride in transforming outdoor spaces through innovative lighting solutions tailored to your vision. From landscape and holiday lighting to permanent installations, our effortless process and expert design deliver breathtaking results and lasting curb appeal. Backed by a lifetime warranty and quarterly service options, our commitment to quality and customer satisfaction is unwavering.</p>
<p class="abs about-quote">Try before you buy and experience your home in a whole new light with our complimentary demo kit — see the stunning effects before you decide.</p>
<a class="btn btn-amber" href="#" style="left:597px;top:1230px;width:181px;height:44px">Learn More &rsaquo;</a>

<div class="perk perk-teal">
  <div class="perk-icon" style="background:var(--teal)">
    <svg width="40" height="40" viewBox="0 0 40 40" fill="none" stroke="#fff" stroke-width="2"><rect x="12" y="5" width="20" height="28" rx="2"/><path d="M16 11h12M16 16h12M16 21h8"/><rect x="5" y="18" width="11" height="16" rx="1.5"/><path d="M8 22h5M8 26h2M11 26h2M8 30h2M11 30h2"/></svg>
  </div>
  <div><h3>We Provide Free Estimate</h3><p>Get a free estimate now</p></div>
</div>
<div class="perk perk-gold">
  <div class="perk-icon" style="background:var(--sun)">
    <svg width="40" height="40" viewBox="0 0 40 40" fill="none" stroke="#3a2c05" stroke-width="2"><path d="M14 4l-2 12M26 4l2 12M14 4h12"/><circle cx="20" cy="25" r="10"/><path d="M20 19l1.8 3.7 4 .6-2.9 2.8.7 4-3.6-1.9-3.6 1.9.7-4-2.9-2.8 4-.6z"/></svg>
  </div>
  <div><h3>We Offering a 10% Discount</h3><p>To military, veterans, and<br>first responders</p></div>
</div>

<!-- SECTORS -->
<div class="abs sectors">
  <div class="sector sector-res" role="img" aria-label="Residential garden steps with path lights under a teal tint">
    <h2>Residential<br>Landscape Lighting</h2>
    <p>Lorem ipsum dolor sit amet, consectetur adipiscing elit, sed do eiusmod tempor incididun</p>
    <a class="btn btn-outline" href="#" style="left:230px;top:342px;width:180px;height:43px">Learn More &rsaquo;</a>
  </div>
  <div class="sector sector-com" role="img" aria-label="Commercial grounds with glowing lights under a golden tint">
    <h2>Commercial<br>Landscape Lighting</h2>
    <p>Lorem ipsum dolor sit amet, consectetur adipiscing elit, sed do eiusmod tempor incididun</p>
    <a class="btn btn-outline-dark" href="#" style="left:219px;top:340px;width:181px;height:43px">Learn More &rsaquo;</a>
  </div>
</div>

<!-- PRODUCTS -->
<div class="eyebrow" style="top:2083px;color:var(--gold)">What We Do</div>
<h2 class="section-title" style="top:2102px;font-weight:400">Products &amp; Services</h2>
<div class="title-rule" style="left:470px;width:270px;top:2156px"></div>

<div class="card-photo card-landscape" role="img" aria-label="Lush garden with path light and ornamental grasses at dusk">
  <div class="card-caption"><span class="accent">Landscape</span><br><span class="plain">Lighting</span></div>
</div>
<div class="card-feature">
  <div class="frame">
    <h3><span style="color:var(--gold)">Holiday</span><br>Lighting</h3>
    <p>Lorem ipsum dolor sit amet, consectetur adipiscing elit, sed do eiusmod tempor incididunt ut labore et dolore magna aliqua. Quis ipsum suspendisse ultrice</p>
    <a class="btn btn-amber" href="#" style="left:90px;top:260px;width:164px;height:39px">Learn More &rsaquo;</a>
  </div>
</div>
<div class="card-photo card-permanent" role="img" aria-label="Two-storey home with permanent roofline lighting at twilight">
  <div class="card-caption"><span class="accent">Permanent</span><br><span class="plain">Installations</span></div>
</div>

<!-- WHY -->
<section class="abs why">
  <div class="eyebrow-left">Outdoor Lighting</div>
  <h2>Why Outdoor<br>Lighting</h2>
  <div class="title-rule" style="left:110px;width:160px;top:213px"></div>
  <p class="copy" style="top:253px">Outdoor Lighting not only beautifies spaces but also significantly enhances safety by illuminating your home or business.</p>
  <p class="copy" style="top:348px">Beautifully lit entrances deter potential intruders, making your home a safer place for your loved ones. we also offer quarterly service plans to ensure lighting equipment continues to operate &amp; illuminate effectively throughout the year.</p>
  <a class="btn btn-amber" href="#" style="left:108px;top:497px;width:165px;height:40px">Learn More &rsaquo;</a>
</section>
<div class="abs why-photo" role="img" aria-label="Home at dusk with walkway and uplit facade"></div>
<svg class="abs" style="left:570px;top:2740px" width="170" height="450" viewBox="0 0 170 450" aria-hidden="true"><line x1="160" y1="5" x2="8" y2="440" stroke="#E5A928" stroke-width="3"/></svg>

<!-- FOOTER BASE -->
<footer class="abs site-footer"></footer>

<!-- ESTIMATE FORM -->
<section class="abs estimate" id="estimate">
  <div class="eyebrow">Contact Us</div>
  <h2 class="section-title" style="font-weight:400">Schedule Free Estimate</h2>
  <div class="title-rule" style="left:335px;width:275px;top:150px;background:linear-gradient(90deg,rgba(255,255,255,0),#fff 25%,#fff 75%,rgba(255,255,255,0))"></div>

  <div class="field" style="left:102px;top:184px;width:359px">
    <svg width="14" height="14" viewBox="0 0 14 14" fill="#333"><circle cx="7" cy="4" r="3"/><path d="M1 14c0-4 3-6 6-6s6 2 6 6z"/></svg>First Name</div>
  <div class="field" style="left:473px;top:184px;width:359px">
    <svg width="14" height="14" viewBox="0 0 14 14" fill="#333"><circle cx="7" cy="4" r="3"/><path d="M1 14c0-4 3-6 6-6s6 2 6 6z"/></svg>Last Name</div>
  <div class="field" style="left:102px;top:247px;width:359px">
    <svg width="14" height="12" viewBox="0 0 14 12" fill="#333"><rect x="0" y="1" width="14" height="10" rx="1"/><path d="M0 2l7 5 7-5" stroke="#fff" stroke-width="1.2" fill="none"/></svg>Email address</div>
  <div class="field" style="left:473px;top:247px;width:359px">
    <svg width="14" height="14" viewBox="0 0 14 14" fill="#333"><path d="M3 1l2.5 3-1.5 1.5c.8 1.8 2.3 3.3 4.1 4.1L9.5 8l3 2.5-1.5 2.5C6 13 1 8 1 2.5z"/></svg>Phone number</div>
  <div class="field" style="left:102px;top:306px;width:730px;height:116px;align-items:flex-start;padding-top:16px">
    <svg width="14" height="13" viewBox="0 0 14 13" fill="#333"><ellipse cx="7" cy="5.5" rx="7" ry="5"/><path d="M2 9l-1 4 4-2.5z"/></svg>Leave Message</div>
  <a class="btn btn-forest" href="#" style="left:362px;top:449px;width:210px;height:48px;font-size:14px">Send Message &rsaquo;</a>
</section>

<!-- FOOTER CONTENT -->
<div class="abs brand footer-brand">Corwin Beacon Lighting</div>
<div class="abs footer-rule" style="top:4042px"></div>
<nav class="abs footer-nav">
  <a href="#">HOME</a><span class="dot"></span>
  <a href="#">ABOUT US</a><span class="dot"></span>
  <a href="#">SERVICES</a><span class="dot"></span>
  <a href="#">PRODUCTS</a><span class="dot"></span>
  <a href="#">GALLERY</a><span class="dot"></span>
  <a href="#">CONTACT</a>
</nav>
<div class="abs footer-rule" style="top:4111px"></div>

<div class="contact-item" style="left:206px">
  <span class="badge"><svg width="14" height="18" viewBox="0 0 14 18" fill="#fff"><path d="M7 0a7 7 0 0 0-7 7c0 5 7 11 7 11s7-6 7-11a7 7 0 0 0-7-7zm0 10a3 3 0 1 1 0-6 3 3 0 0 1 0 6z"/></svg></span>123 Street Address line</div>
<div class="contact-item" style="left:488px">
  <span class="badge"><svg width="16" height="16" viewBox="0 0 14 14" fill="#fff"><path d="M3 1l2.5 3-1.5 1.5c.8 1.8 2.3 3.3 4.1 4.1L9.5 8l3 2.5-1.5 2.5C6 13 1 8 1 2.5z"/></svg></span>(318) 555-0142</div>
<div class="contact-item" style="left:690px">
  <span class="badge"><svg width="16" height="13" viewBox="0 0 14 12" fill="#fff"><rect x="0" y="1" width="14" height="10" rx="1"/><path d="M0 2l7 5 7-5" stroke="#FFC000" stroke-width="1.2" fill="none"/></svg></span>enquiry@corwinbeacon.com</div>

<a class="social" href="#" aria-label="Social profile 1" style="left:947px"></a>
<a class="social" href="#" aria-label="Social profile 2" style="left:985px"></a>
<a class="social" href="#" aria-label="Social profile 3" style="left:1023px"></a>
<a class="social" href="#" aria-label="Social profile 4" style="left:1063px"></a>

<div class="abs copyright">Copyright © 2025 Corwin Beacon &nbsp;| &nbsp;All Right Reserved</div>

</body>
</html>
```